Heron Haulage needs Bussiness cards!

Our new trucking company needs business cards!
We need the same design with two different names and emails, everything else it's the same.
I have included our original logo so we can use it for the design.
Note: the logo to be used is the o e with the buffalo on the right side, next to the letters H and H.

Target Market(s)

Trucking, refrigerated transportation, freight

Industry/Entity Type

Business

Contact Information for Business Card

Card #1:
Marcus Whitfield
marcuswhitfield@heronhaulage.example
1-855-317-6094
(555)238-7160
4117 W. Larkin Ave.
Corvale, NV 78590
www.heronhaulage.example

Card#2:
Rosalba Quintero
rosalba@heronhaulage.example
1-855-317-6094
(555)238-7160
4117 W. Larkin Ave.
Corvale, NV 78590
www.heronhaulage.example

Font styles to use
Sans Serif

Colors
0655a3
ec1f27
ffffff

Requirements
Must have
• our logo
Nice to have
• roads on background,

```html
<!DOCTYPE html>
<html lang="en">
<head>
<meta charset="utf-8">
<title>Heron Haulage – Business Cards</title>
<link rel="stylesheet" href="https://fonts.googleapis.com/css2?family=Roboto+Slab:wght@400;500&family=Roboto:wght@900&display=swap">
<style>
  :root {
    --navy: #0d3566;
    --red: #c4161c;
    --white: #ffffff;
    --ink: #1c1c1c;
    --backdrop: #e9e6e1;
    --road-dark: #1b2a3a;
    --road-mid: #3d5066;
    --road-light: #8c9aa6;
  }
  * { margin: 0; padding: 0; box-sizing: border-box; }
  html, body { width: 1200px; height: 913px; overflow: hidden; }
  body {
    background: var(--backdrop);
    position: relative;
    font-family: "Roboto Slab", Georgia, serif;
  }
  .card {
    position: absolute;
    width: 560px;
    height: 320px;
    background: var(--white);
    box-shadow: 0 6px 18px rgba(0,0,0,.18);
    overflow: hidden;
  }
  .card--front { left: 80px; top: 90px; }
  .card--back { left: 560px; top: 503px; }

  /* front */
  .front-art { position: absolute; inset: 0; width: 100%; height: 100%; }
  .brand {
    position: absolute;
    left: 44px;
    top: 72px;
    display: flex;
    align-items: center;
    gap: 10px;
  }
  .brand__dot {
    width: 20px; height: 20px;
    border-radius: 50%;
    background: var(--red);
    flex: none;
  }
  .brand__name {
    font-family: "Roboto", Arial, sans-serif;
    font-weight: 900;
    font-size: 34px;
    letter-spacing: -0.5px;
    color: var(--navy);
    line-height: 1;
    white-space: nowrap;
  }

  /* back */
  .mark-disc {
    position: absolute;
    right: 34px;
    top: 28px;
    width: 170px;
    height: 170px;
    border-radius: 50%;
    background: var(--navy);
  }
  .holder {
    position: absolute;
    left: 40px;
    top: 96px;
    width: 300px;
  }
  .holder__name {
    font-size: 26px;
    font-weight: 400;
    color: var(--red);
    padding-bottom: 6px;
    border-bottom: 2px solid var(--red);
    white-space: nowrap;
  }
  .contacts { list-style: none; margin-top: 10px; }
  .contacts li {
    display: flex;
    align-items: center;
    gap: 10px;
    font-size: 13.5px;
    color: var(--ink);
    line-height: 22px;
    white-space: nowrap;
  }
  .icon {
    width: 15px; height: 15px;
    flex: none;
  }
  .address {
    position: absolute;
    left: 40px;
    bottom: 40px;
    display: flex;
    align-items: center;
    gap: 10px;
    font-size: 13.5px;
    line-height: 19px;
    color: var(--ink);
  }
</style>
</head>
<body>

<section class="card card--front" aria-label="Card front">
  <svg class="front-art" viewBox="0 0 560 320" preserveAspectRatio="none">
    <defs>
      <linearGradient id="roadTone" x1="0" y1="0" x2="1" y2="1">
        <stop offset="0" stop-color="var(--road-light)"/>
        <stop offset=".45" stop-color="var(--road-mid)"/>
        <stop offset="1" stop-color="var(--road-dark)"/>
      </linearGradient>
    </defs>
    <polygon points="0,320 0,268 560,70 560,320" fill="url(#roadTone)" role="img" aria-label="Photo of an open road leading into snowy mountains"/>
    <line x1="0" y1="266" x2="560" y2="68" stroke="var(--red)" stroke-width="4"/>
  </svg>
  <div class="brand">
    <span class="brand__dot"></span>
    <span class="brand__name">Heron Haulage</span>
  </div>
</section>

<section class="card card--back" aria-label="Card back">
  <div class="mark-disc"></div>
  <div class="holder">
    <h1 class="holder__name">Marcus Whitfield</h1>
    <ul class="contacts">
      <li>
        <svg class="icon" viewBox="0 0 16 16"><circle cx="8" cy="8" r="8" fill="var(--red)"/><path d="M5 4.5l1.6-.4 1 2-1 .8a5 5 0 0 0 2.5 2.5l.8-1 2 1-.4 1.6C8 11.3 4.7 8 5 4.5z" fill="var(--white)"/></svg>
        1-855-317-6094
      </li>
      <li>
        <svg class="icon" viewBox="0 0 16 16"><circle cx="8" cy="8" r="8" fill="var(--red)"/><rect x="5.5" y="3.5" width="5" height="9" rx="1" fill="var(--white)"/><rect x="6.5" y="5" width="3" height="5" fill="var(--red)"/></svg>
        (555)238-7160
      </li>
      <li>
        <svg class="icon" viewBox="0 0 16 16"><circle cx="8" cy="8" r="8" fill="var(--red)"/><rect x="4" y="5" width="8" height="6" fill="var(--white)"/><path d="M4 5l4 3.5L12 5" fill="none" stroke="var(--red)" stroke-width="1"/></svg>
        marcuswhitfield@heronhaulage.example
      </li>
      <li>
        <svg class="icon" viewBox="0 0 16 16"><circle cx="8" cy="8" r="8" fill="var(--red)"/><circle cx="8" cy="8" r="4.2" fill="none" stroke="var(--white)" stroke-width="1"/><path d="M3.8 8h8.4M8 3.8c-2 2.4-2 6 0 8.4M8 3.8c2 2.4 2 6 0 8.4" fill="none" stroke="var(--white)" stroke-width="1"/></svg>
        www.heronhaulage.example
      </li>
    </ul>
  </div>
  <div class="address">
    <svg class="icon" viewBox="0 0 16 16"><circle cx="8" cy="8" r="8" fill="var(--red)"/><path d="M4 8.2L8 4.5l4 3.7h-1.2V11.5H9V9.3H7v2.2H5.2V8.2z" fill="var(--white)"/></svg>
    <span>4117 W. Larkin Ave.<br>Corvale, NV 78590</span>
  </div>
</section>

</body>
</html>
```